Bright Harbor Counseling Letterhead for hip modern business

I would like some ombre use of the colors in the logo hip letterhead that incorporates logo colors and feel, needs to connect with young professionals and college students. i need to be able to write letters to schools to excuse absences as well. i like color blocks on one side preferably using colors from the attached logo design.

Target Market(s)

high income young people, young adults and college students

Industry/Entity Type

mental health

Font styles to use
Serif
Sans Serif

Colors
0054AA
0677BA
7BADD7
CADEEF
E8F1F8
0094D4
00A9DD
6FCCEA
C7EBF8
E9F6FB
00AB8E
00BBA5
67D7C9
C6EFE9
E9F9F6
59FF00
82FF00
B8FF75
E3FFCB
F4FFEA
A7469A
B969AE
D3A5CF
EDDBEB
F8F0F9
6B429C
8869AF
B7A5CE
E3DAEB
F3F0F8

Requirements
Must have
• a modern hip feel, somewhat color

```html
<!DOCTYPE html>
<html lang="en">
<head>
<meta charset="UTF-8">
<title>Bright Harbor Counseling — Letterhead</title>
<link rel="stylesheet" href="https://fonts.googleapis.com/css2?family=Arimo:wght@400&display=swap">
<style>
  :root {
    --backdrop: #7f9a98;
    --paper: #ececec;
    --ink: #2a2a30;
    --band-purple: #7b2a88;
    --band-text: #ffffff;
  }
  html, body {
    margin: 0;
    padding: 0;
    width: 1200px;
    height: 960px;
    overflow: hidden;
    background: var(--backdrop);
  }
  .letterhead {
    position: absolute;
    left: 280px;
    top: 28px;
    width: 640px;
    height: 904px;
    background: var(--paper);
    overflow: hidden;
  }
  .brand {
    position: absolute;
    left: 46px;
    top: 84px;
    margin: 0;
    font-family: "Arimo", sans-serif;
    font-weight: 400;
    font-size: 22px;
    line-height: 1;
    color: var(--ink);
    white-space: nowrap;
  }
  .corner-wash {
    position: absolute;
    left: 0;
    bottom: 36px;
    width: 190px;
    height: 132px;
    background: linear-gradient(135deg,
      rgba(0,169,221,0.55) 0%,
      rgba(6,119,186,0.6) 35%,
      rgba(136,105,175,0.65) 65%,
      rgba(167,70,154,0.7) 100%);
    border-top-right-radius: 60px;
  }
  .contact-band {
    position: absolute;
    left: 0;
    bottom: 0;
    width: 100%;
    height: 36px;
    background: var(--band-purple);
    font-family: "Arimo", sans-serif;
    font-size: 9.5px;
    color: var(--band-text);
  }
  .contact-item {
    position: absolute;
    top: 0;
    height: 36px;
    display: flex;
    align-items: center;
    gap: 5px;
    white-space: nowrap;
  }
  .contact-address { left: 92px; }
  .contact-phone { left: 323px; }
  .contact-email { left: 420px; }
  .contact-icon {
    width: 9px;
    height: 9px;
    flex: none;
  }
</style>
</head>
<body>
  <main class="letterhead">
    <h1 class="brand">Bright Harbor Counseling</h1>

    <div class="corner-wash" role="img" aria-label="Soft blue, teal and purple colour wash decoration"></div>

    <footer class="contact-band">
      <span class="contact-item contact-address">48 Elm Row, Ste 210, Fairhaven, TX 75321</span>
      <span class="contact-item contact-phone">
        <svg class="contact-icon" viewBox="0 0 10 10" aria-hidden="true">
          <circle cx="5" cy="5" r="5" fill="#ffffff"/>
          <path d="M3.2 2.6 L4.1 2.5 L4.5 3.8 L3.9 4.2 Q4.5 5.5 5.8 6.1 L6.2 5.5 L7.5 5.9 L7.4 6.8 Q5.6 7.4 4 5.9 Q2.6 4.4 3.2 2.6 Z" fill="var(--band-purple)"/>
        </svg>
        214 555 0187
      </span>
      <span class="contact-item contact-email">
        <svg class="contact-icon" viewBox="0 0 10 10" aria-hidden="true">
          <circle cx="5" cy="5" r="5" fill="#ffffff"/>
          <rect x="2.5" y="3.2" width="5" height="3.6" fill="none" stroke="var(--band-purple)" stroke-width="0.8"/>
          <path d="M2.5 3.2 L5 5.2 L7.5 3.2" fill="none" stroke="var(--band-purple)" stroke-width="0.8"/>
        </svg>
        hello@brightharbor.example
      </span>
    </footer>
  </main>
</body>
</html>
```